Animal Eye Clinic needs a Business card

We are a new veterinary ophthalmology practice (Ridgeline Pet Vision Care) and we need a business card designed. We only see animal eyes - we are not a regular veterinary clinic. We already have a logo. We are looking for a professional, good looking business card to hand out to our clients. We are looking for something simple but professional and contemporary. Our logo is likely the only picture/graphic that needs to be on the card.
Updates

Contact Information for Business Card

Delia Vossman, BSc, DVM, MSc, DipACVO
Veterinary Ophthalmologist

Phone: 250.418.3927
Email: ridgelinepetvisioncare@mailbox-example.net
Website: ridgelinepetvisioncare-example.net
Address: 1874 Thornbury Rd
Kelowna, BC, V1X 4M9

Colors

Designer to choose colors to be used in the design.

Requirements
Must have
• Our logo (attached)

```html
<!DOCTYPE html>
<html lang="en">
<head>
<meta charset="utf-8">
<title>Ridgeline Pet Vision Care – Business Card</title>
<link rel="stylesheet" href="https://fonts.googleapis.com/css2?family=Roboto:ital,wght@0,300;0,400;0,500;0,700;1,500&display=swap">
<style>
  :root {
    --page-bg: #e9e7e4;
    --card-bg: #2b2b2d;
    --card-edge: #1a9fb0;
    --teal: #1a9fb0;
    --text-light: #e6e6e6;
    --rule: #cfcfcf;
  }
  * { box-sizing: border-box; margin: 0; padding: 0; }
  html, body {
    width: 1200px; height: 796px; overflow: hidden;
    background: var(--page-bg);
    font-family: "Roboto", Arial, sans-serif;
  }
  .canvas {
    position: relative; width: 1200px; height: 796px;
  }
  .card {
    position: absolute;
    width: 540px; height: 309px;
    background: var(--card-bg);
    border-left: 3px solid var(--card-edge);
    border-bottom: 3px solid var(--card-edge);
    box-shadow: 0 6px 18px rgba(0,0,0,0.25);
  }
  .card--front { left: 40px; top: 160px; }
  .card--back { left: 620px; top: 327px; }

  .brand { display: flex; align-items: center; gap: 12px; }
  .brand__dot {
    flex: none; width: 44px; height: 44px; border-radius: 50%;
    background: var(--teal);
  }
  .brand__name {
    color: var(--teal); font-weight: 500; text-transform: uppercase;
    line-height: 1.05;
  }
  .card--front .brand {
    position: absolute; left: 50%; top: 50%;
    transform: translate(-50%, -50%);
  }
  .card--front .brand__name { font-size: 26px; letter-spacing: 1px; }
  .card--front .brand__dot { width: 58px; height: 58px; }

  .card--back .brand { position: absolute; right: 30px; top: 38px; gap: 9px; }
  .card--back .brand__name { font-size: 15px; letter-spacing: .5px; }
  .card--back .brand__dot { width: 34px; height: 34px; }

  .person { position: absolute; left: 30px; top: 108px; }
  .person__name { color: var(--teal); font-size: 15px; }
  .person__name strong { font-weight: 700; font-style: italic; }
  .person__title { color: var(--text-light); font-size: 12px; font-weight: 300; margin-top: 2px; }

  .rule {
    position: absolute; left: 30px; right: 30px; top: 158px;
    height: 1px; background: var(--rule);
  }

  .contact { position: absolute; left: 30px; top: 172px; list-style: none; }
  .contact__item {
    display: flex; align-items: center; gap: 7px;
    color: var(--text-light); font-size: 11.5px; font-weight: 300;
    line-height: 19px;
  }
  .contact__item svg { width: 11px; height: 11px; fill: var(--text-light); flex: none; }
  .contact__accent { color: var(--teal); }

  .address {
    position: absolute; right: 30px; bottom: 26px; text-align: right;
    color: var(--text-light); font-size: 12px; font-weight: 300; line-height: 17px;
    font-style: normal;
  }
</style>
</head>
<body>
<main class="canvas">

  <section class="card card--front" aria-label="Card front">
    <div class="brand">
      <span class="brand__dot"></span>
      <p class="brand__name">Ridgeline<br>Pet Vision Care</p>
    </div>
  </section>

  <section class="card card--back" aria-label="Card back">
    <div class="brand">
      <span class="brand__dot"></span>
      <p class="brand__name">Ridgeline<br>Pet Vision Care</p>
    </div>

    <div class="person">
      <p class="person__name"><strong>Delia Vossman</strong>, BSc, DVM, MSc, DipACVO</p>
      <p class="person__title">Veterinary Ophthalmologist</p>
    </div>

    <div class="rule"></div>

    <ul class="contact">
      <li class="contact__item">
        <svg viewBox="0 0 24 24" aria-hidden="true"><path d="M6.6 10.8a15.1 15.1 0 0 0 6.6 6.6l2.2-2.2a1 1 0 0 1 1-.25 11.4 11.4 0 0 0 3.6.57 1 1 0 0 1 1 1V20a1 1 0 0 1-1 1A17 17 0 0 1 3 4a1 1 0 0 1 1-1h3.5a1 1 0 0 1 1 1c0 1.25.2 2.45.57 3.57a1 1 0 0 1-.25 1z"/></svg>
        250.418.3927
      </li>
      <li class="contact__item">
        <svg viewBox="0 0 24 24" aria-hidden="true"><path d="M2 5h20v14H2z M2 5l10 8 10-8" fill="none" stroke="#e6e6e6" stroke-width="2"/></svg>
        ridgelinepetvisioncare@mailbox-example.net
      </li>
      <li class="contact__item">
        <svg viewBox="0 0 24 24" aria-hidden="true"><circle cx="12" cy="12" r="10" fill="none" stroke="#e6e6e6" stroke-width="2"/><path d="M2 12h20M12 2c3 3 3 17 0 20M12 2c-3 3-3 17 0 20" fill="none" stroke="#e6e6e6" stroke-width="1.6"/></svg>
        <span>www.<span class="contact__accent">ridgelinepetvisioncare</span>-example.net</span>
      </li>
    </ul>

    <address class="address">
      1874 Thornbury Rd<br>
      Kelowna, BC, V1X 4M9
    </address>
  </section>

</main>
</body>
</html>
```